Business Card Design Project

Looking to update our business cards. We have a logo with our slogan. We are an IT firm so we wouldlike a modern look.

Industry/Entity Type

Business

```html
<!DOCTYPE html>
<html lang="en">
<head>
<meta charset="utf-8">
<title>Nexora Business Card</title>
<link href="https://fonts.googleapis.com/css2?family=Jost:wght@400;500;600&display=swap" rel="stylesheet">
<style>
  :root {
    --backdrop: #5c3d26;
    --card: #dccab0;
    --ink: #1c1a17;
    --green: #68873a;
    --lime: #a8c53e;
    --white: #ffffff;
  }
  * { box-sizing: border-box; margin: 0; padding: 0; }
  html, body { width: 1200px; height: 788px; overflow: hidden; }
  body {
    background: var(--backdrop);
    font-family: "Jost", "Futura", sans-serif;
    color: var(--ink);
    position: relative;
  }
  .card {
    position: absolute;
    width: 524px;
    height: 300px;
    border-radius: 18px;
    background: var(--card);
    overflow: hidden;
    box-shadow: 0 4px 12px rgba(0,0,0,0.35);
  }
  .card--front { left: 362px; top: 33px; }
  .card--back { left: 69px; top: 465px; }
  .card__face { position: absolute; inset: 0; }
  .card--back .card__face { transform: scaleX(-1); }
  .band { position: absolute; inset: 0; width: 100%; height: 100%; }
  .brand {
    position: absolute;
    left: 0; right: 0; top: 58px;
    text-align: center;
  }
  .brand__name {
    font-size: 38px;
    font-weight: 600;
    letter-spacing: 6px;
    color: var(--green);
    line-height: 1;
  }
  .brand__tagline {
    margin-top: 8px;
    font-size: 11px;
    font-weight: 600;
    letter-spacing: 2px;
    color: var(--ink);
  }
  .contacts {
    position: absolute;
    left: 80px; top: 168px;
    list-style: none;
    font-size: 14px;
    line-height: 22px;
  }
  .contacts li { display: flex; align-items: center; gap: 7px; }
  .contacts svg { width: 12px; height: 12px; flex: none; }
  .address {
    position: absolute;
    right: 72px; top: 198px;
    font-style: normal;
    text-align: right;
    font-size: 14px;
    line-height: 18px;
  }
  .band-label {
    position: absolute;
    color: var(--white);
    font-size: 17px;
    white-space: nowrap;
  }
  .band-label small { font-size: 13px; }
  .card--front .band-label { left: 242px; top: 268px; }
  .card--back .band-label { left: 119px; top: 270px; font-size: 16px; }
</style>
</head>
<body>

<section class="card card--front" aria-label="Card front">
  <svg class="band" viewBox="0 0 524 300" preserveAspectRatio="none" aria-hidden="true">
    <path d="M0 300 V292 C150 280 300 262 524 256 V300 Z" fill="var(--green)"/>
    <path d="M0 280 C110 272 190 268 262 266 C170 272 80 282 0 293 Z" fill="var(--lime)"/>
  </svg>
  <div class="card__face">
    <div class="brand">
      <div class="brand__name">NEXORA</div>
      <div class="brand__tagline">MAKING TECHNOLOGY EASY</div>
    </div>
    <ul class="contacts">
      <li><svg viewBox="0 0 12 12"><circle cx="6" cy="6" r="5.2" fill="none" stroke="var(--ink)" stroke-width="1.2"/><path d="M4 3.5 L5 5.5 L4.5 6.5 L6 8 L7 7.5 L8.5 8.5" fill="none" stroke="var(--ink)" stroke-width="1.2"/></svg>+12 345 67890</li>
      <li><svg viewBox="0 0 12 12"><rect x="1" y="5" width="10" height="5" rx="1" fill="var(--ink)"/><path d="M3 5 L4 2 H8 L9 5" fill="none" stroke="var(--ink)" stroke-width="1.2"/></svg>+12 345 67890</li>
      <li><svg viewBox="0 0 12 12"><rect x="1" y="2.5" width="10" height="7" rx="1" fill="var(--ink)"/><path d="M1.5 3 L6 7 L10.5 3" fill="none" stroke="var(--card)" stroke-width="1"/></svg>info@website.com</li>
      <li><svg viewBox="0 0 12 12"><circle cx="6" cy="6" r="5" fill="none" stroke="var(--ink)" stroke-width="1.1"/><ellipse cx="6" cy="6" rx="2.2" ry="5" fill="none" stroke="var(--ink)" stroke-width="1"/><path d="M1 6 H11" stroke="var(--ink)" stroke-width="1"/></svg>www.website.com</li>
    </ul>
    <address class="address">#0000, Street Name<br>Area Name<br>Country Code</address>
  </div>
  <div class="band-label">Your Name, <small>Designation</small></div>
</section>

<section class="card card--back" aria-label="Card back">
  <div class="card__face">
    <svg class="band" viewBox="0 0 524 300" preserveAspectRatio="none" aria-hidden="true">
      <path d="M0 300 V292 C150 280 300 262 524 256 V300 Z" fill="var(--green)"/>
      <path d="M0 280 C110 272 190 268 262 266 C170 272 80 282 0 293 Z" fill="var(--lime)"/>
    </svg>
    <div class="brand">
      <div class="brand__name">NEXORA</div>
      <div class="brand__tagline">MAKING TECHNOLOGY EASY</div>
    </div>
    <ul class="contacts">
      <li><svg viewBox="0 0 12 12"><circle cx="6" cy="6" r="5.2" fill="none" stroke="var(--ink)" stroke-width="1.2"/><path d="M4 3.5 L5 5.5 L4.5 6.5 L6 8 L7 7.5 L8.5 8.5" fill="none" stroke="var(--ink)" stroke-width="1.2"/></svg>+12 345 67890</li>
      <li><svg viewBox="0 0 12 12"><rect x="1" y="5" width="10" height="5" rx="1" fill="var(--ink)"/><path d="M3 5 L4 2 H8 L9 5" fill="none" stroke="var(--ink)" stroke-width="1.2"/></svg>+12 345 67890</li>
      <li><svg viewBox="0 0 12 12"><rect x="1" y="2.5" width="10" height="7" rx="1" fill="var(--ink)"/><path d="M1.5 3 L6 7 L10.5 3" fill="none" stroke="var(--card)" stroke-width="1"/></svg>info@website.com</li>
      <li><svg viewBox="0 0 12 12"><circle cx="6" cy="6" r="5" fill="none" stroke="var(--ink)" stroke-width="1.1"/><ellipse cx="6" cy="6" rx="2.2" ry="5" fill="none" stroke="var(--ink)" stroke-width="1"/><path d="M1 6 H11" stroke="var(--ink)" stroke-width="1"/></svg>www.website.com</li>
    </ul>
    <address class="address">#0000, Street Name<br>Area Name<br>Country Code</address>
  </div>
  <div class="band-label">www.website.com</div>
</section>

</body>
</html>
```